Criação de Cartao de Visita para Lírio & Cobre
A empresa queria:
" Venda de Suplementos Alimentares/Nutricionais, principalmente via whatsapp e facebook, fazemos entregas e aceitamos cartões. Ainda não possuimos loja física. Cobrimos qualquer oferta de site ou loja nacional. "

```html
<!DOCTYPE html>
<html lang="pt-BR">
<head>
<meta charset="UTF-8">
<title>Lírio & Cobre — Cartão de Visita</title>
<link href="https://fonts.googleapis.com/css2?family=Montserrat:wght@500;600;700;800&display=swap" rel="stylesheet">
<style>
  :root {
    --page: #e9e7e4;
    --white: #ffffff;
    --ink: #1b1b1b;
    --graphite: #4a4a4a;
    --graphite-dark: #2e2e2e;
    --gold: #d9a43a;
    --gold-light: #f0c868;
    --gold-deep: #b07e22;
    --muted: #555555;
  }
  * { margin: 0; padding: 0; box-sizing: border-box; }
  html, body { width: 1200px; height: 1200px; overflow: hidden; }
  body {
    background: var(--page);
    font-family: "Montserrat", Arial, sans-serif;
    display: flex;
    flex-direction: column;
    align-items: center;
    justify-content: center;
    gap: 44px;
  }
  .card {
    position: relative;
    width: 900px;
    height: 514px;
    overflow: hidden;
    box-shadow: 0 10px 30px rgba(0,0,0,0.18);
  }

  /* Frente */
  .card--front { background: var(--white); }
  .brand {
    position: absolute;
    display: flex;
    align-items: center;
    gap: 18px;
  }
  .brand__dot {
    width: 40px; height: 40px;
    border-radius: 50%;
    background: var(--gold);
  }
  .brand__name {
    font-weight: 800;
    color: var(--gold);
    letter-spacing: 0.5px;
    white-space: nowrap;
  }
  .card--front .brand { left: 70px; top: 200px; }
  .card--front .brand__name { font-size: 44px; }

  .contact {
    position: absolute;
    right: 50px;
    top: 92px;
    text-align: right;
  }
  .contact__person { margin-bottom: 20px; padding-right: 46px; }
  .contact__name {
    font-size: 15px; font-weight: 600; letter-spacing: 2px; color: var(--muted);
  }
  .contact__role {
    font-size: 11px; font-weight: 500; letter-spacing: 1.5px; color: var(--muted);
  }
  .contact__list { list-style: none; }
  .contact__item {
    display: flex;
    justify-content: flex-end;
    align-items: center;
    gap: 12px;
    margin-bottom: 10px;
    font-size: 16px;
    font-weight: 700;
    color: var(--ink);
    line-height: 1.15;
  }
  .contact__icon {
    flex: none;
    width: 30px; height: 30px;
    background: var(--gold);
    display: flex; align-items: center; justify-content: center;
  }
  .contact__icon svg { width: 18px; height: 18px; }

  .edge { position: absolute; left: 0; bottom: 0; width: 100%; height: 110px; }

  /* Verso */
  .card--back {
    background: linear-gradient(115deg, var(--graphite) 0%, var(--graphite) 40%, var(--graphite-dark) 41%, var(--graphite-dark) 58%, var(--graphite) 59%, var(--graphite) 100%);
  }
  .card--back .brand {
    left: 50%; top: 44%;
    transform: translate(-50%, -50%);
  }
  .card--back .brand__name { font-size: 56px; }
  .card--back .brand__dot { width: 48px; height: 48px; }
</style>
</head>
<body>

  <section class="card card--front" aria-label="Frente do cartão">
    <div class="brand">
      <span class="brand__dot"></span>
      <span class="brand__name">Lírio &amp; Cobre</span>
    </div>

    <div class="contact">
      <div class="contact__person">
        <p class="contact__name">NOME SOBRENOME</p>
        <p class="contact__role">FUNÇÃO</p>
      </div>
      <ul class="contact__list">
        <li class="contact__item">contato@liriocobre.com.br
          <span class="contact__icon"><svg viewBox="0 0 24 24" fill="none" stroke="#fff" stroke-width="2"><rect x="3" y="6" width="18" height="12"/><path d="M3 6l9 7 9-7"/></svg></span>
        </li>
        <li class="contact__item">www.liriocobre.com.br
          <span class="contact__icon"><svg viewBox="0 0 24 24" fill="none" stroke="#fff" stroke-width="2"><circle cx="12" cy="12" r="9"/><path d="M3 12h18M12 3c3 3 3 15 0 18M12 3c-3 3-3 15 0 18"/></svg></span>
        </li>
        <li class="contact__item">(11) 99999-9999
          <span class="contact__icon"><svg viewBox="0 0 24 24" fill="#fff"><path d="M6.6 10.8a15 15 0 006.6 6.6l2.2-2.2a1 1 0 011-.25 11.4 11.4 0 003.6.6 1 1 0 011 1V20a1 1 0 01-1 1A17 17 0 013 4a1 1 0 011-1h3.5a1 1 0 011 1 11.4 11.4 0 00.6 3.6 1 1 0 01-.25 1z"/></svg></span>
        </li>
        <li class="contact__item">(11) 99999-9999
          <span class="contact__icon"><svg viewBox="0 0 24 24" fill="#fff"><rect x="7" y="2" width="10" height="20" rx="2"/><rect x="9" y="5" width="6" height="11" fill="#d9a43a"/></svg></span>
        </li>
        <li class="contact__item">Endereço Completo, 000 Bairro<br>Cidade/Estado
          <span class="contact__icon"><svg viewBox="0 0 24 24" fill="#fff"><path d="M12 2a7 7 0 00-7 7c0 5 7 13 7 13s7-8 7-13a7 7 0 00-7-7zm0 9.5A2.5 2.5 0 1112 6.5a2.5 2.5 0 010 5z"/></svg></span>
        </li>
      </ul>
    </div>

    <svg class="edge" viewBox="0 0 900 110" preserveAspectRatio="none" aria-hidden="true">
      <polygon points="0,92 430,92 470,110 0,110" fill="var(--gold)"/>
      <polygon points="430,92 900,60 900,110 470,110" fill="var(--gold-light)"/>
      <polygon points="560,100 900,74 900,84 600,108" fill="var(--ink)"/>
      <polygon points="0,86 420,86 430,92 0,92" fill="var(--gold-deep)"/>
    </svg>
  </section>

  <section class="card card--back" aria-label="Verso do cartão">
    <div class="brand">
      <span class="brand__dot"></span>
      <span class="brand__name">Lírio &amp; Cobre</span>
    </div>

    <svg class="edge" viewBox="0 0 900 110" preserveAspectRatio="none" aria-hidden="true">
      <polygon points="0,84 900,84 900,110 0,110" fill="var(--gold)"/>
      <polygon points="0,84 900,84 900,90 0,90" fill="var(--gold-light)"/>
      <polygon points="0,74 380,74 440,84 0,84" fill="var(--ink)"/>
    </svg>
  </section>

</body>
</html>
```